A parent Company needs a website as a leading diversified business in industrial Conglomerates in Af

Velkor Group is a private (Holding) limited liability company incorporated under the Companies Code, 1963 (Act 179) in November, 2013 to following the speedy growth in numbers of its current subsidiaries which has been founded several years ago with an emerging force to become one of the largest and a leading diversified business in industrial Conglomerates in Africa.
The Group which is 100% wholly owned indigenous Ghanaian Company focuses on provision of local, value-added products and services that meet the needs of the African population. The Group is headquartered in Accra, Ghana with interests across a range of sectors in Africa.
We are currently into Food & Beverage, Real Estate Development, Transportation, Health Care, Consumer Products Distribution, Agro Processing, Manufacturing, ICT, Exports & Import, and still counting.
In the next 3 years, we shall announce our ambitions to enter Ghana's largest Oil and Gas industry, playing a strategic role in the petroleum sector with strategic alliances, and help build Ghana's biggest and most important Energy sector in the country.
Inspired by billionaires Tom Prewitt, Harlan Voskel, and Emeka Ofodile, Velkor Group (Velkor Foundation) is committed to making a name for itself on the philanthropic circuit and has given away privately and still given to the cause to the needy in the society and some specific social causes in Ghana.
The company is managed by a 5 member board and a 2 member advisory experts who are non-board members.
The company has a vision, mission and it is guided by its core values.
We would like to see a designs that is very professional and looks corporate and can attract investors and partners. It must communicate financial safety and growth and must reflect our logo colors.

```html
<!DOCTYPE html>
<html lang="en">
<head>
<meta charset="utf-8">
<title>Velkor Group</title>
<link rel="stylesheet" href="https://fonts.googleapis.com/css2?family=Open+Sans:ital,wght@0,400;0,600;0,700;1,400&family=Noto+Serif:ital@1&display=swap">
<style>
:root{
  --blue:#1479bd;
  --blue-dark:#0f68a6;
  --red:#d81f1f;
  --ink:#333;
  --panel:#e4e4e4;
  --bar:#262626;
  --footer:#404040;
  --footer-deep:#353535;
  --footer-text:#c9c9c9;
  --white:#fff;
}
*{margin:0;padding:0;box-sizing:border-box}
html,body{width:891px;height:1200px;overflow:hidden;background:var(--white)}
body{font-family:"Open Sans",Arial,sans-serif;color:var(--ink);position:relative}
.abs{position:absolute}

/* header */
.brand{left:82px;top:32px;display:flex;align-items:center;gap:8px}
.brand-mark{width:26px;height:26px;border-radius:50%;background:var(--blue)}
.brand-name{font-size:20px;font-weight:600;color:var(--blue);letter-spacing:.5px}
.search-label{left:608px;top:16px;font-size:11px;color:#555}
.search-frame{left:608px;top:36px;width:202px;height:48px;background:#2f8ed4;border-radius:3px}
.search-box{left:620px;top:48px;width:178px;height:26px;background:var(--white);border:1px solid #1f5f92;font-size:9px;color:#999;padding:6px 5px}
.search-icon{left:782px;top:55px}

/* nav */
.nav{left:73px;top:110px;width:746px;height:48px;background:var(--bar);border-radius:10px 10px 0 0}
.nav-item{position:absolute;top:11px;height:27px;font-size:12.5px;color:var(--white);line-height:25px;text-align:center;white-space:nowrap;background:linear-gradient(#7a7a7a,#4e4e4e);border:1px solid #8a8a8a;border-radius:2px}
.nav-item.is-active{background:var(--red);border-color:#f05050;font-weight:600}
.social{top:14px;width:20px;height:20px;border-radius:2px;position:absolute}

/* hero */
.hero{left:73px;top:158px;width:746px;height:409px;background:linear-gradient(120deg,#a69888 0%,#d8cfc4 30%,#8b8a8e 55%,#e6e3df 80%,#c9c2ba 100%)}
.welcome{left:97px;top:249px;width:346px;height:161px;background:rgba(245,243,241,.9)}
.welcome h1{position:absolute;left:11px;top:10px;font-size:24px;font-weight:400;color:#333;white-space:nowrap}
.welcome h1 span{color:var(--blue)}
.welcome p{position:absolute;left:12px;top:50px;width:325px;font-size:11px;line-height:14px;color:#444}
.btn-red{position:absolute;left:12px;top:118px;height:27px;padding:0 9px;background:var(--red);color:var(--white);font-size:12px;line-height:27px;display:flex;gap:7px;align-items:center}
.dots{left:96px;top:543px;display:flex;gap:2px}
.dots i{width:7px;height:7px;border-radius:50%;background:var(--white)}
.dots i.on{background:var(--blue)}

/* feature band */
.features{left:73px;top:580px;width:746px;height:97px;background:linear-gradient(#2c8cd0,var(--blue-dark));display:flex}
.feature{position:relative;height:97px;border-right:1px solid rgba(255,255,255,.25);color:var(--white)}
.feature:last-child{border-right:none}
.feature h2{position:absolute;top:10px;font-size:19px;font-weight:600}
.feature p{position:absolute;top:42px;font-size:8.5px;line-height:13px;width:150px}
.feature a{position:absolute;top:73px;font-size:9px;color:var(--white)}
.feature svg{position:absolute}

/* about */
.about{left:73px;top:689px;width:746px;height:252px;background:var(--panel)}
.about-photo{left:92px;top:714px;width:115px;height:114px;background:linear-gradient(135deg,#8c7a6c,#3c3a40 60%,#b7aea3);border:2px solid var(--white)}
.about-title,.testi-title{font-size:19px;font-weight:400;color:#333}
.about-title{left:219px;top:711px}
.about-title span{color:var(--blue)}
.about-lead{left:217px;top:742px;width:318px;font-size:9px;line-height:13.5px;color:#555}
.about-body{left:92px;top:843px;width:450px;font-size:9px;line-height:14px;color:#555}
.about-more{left:93px;top:905px;font-size:9.5px;color:var(--red);font-style:italic;text-decoration:underline}
.testi-title{left:590px;top:711px}
.rule{height:1px;background:#cfcfcf}
.testi-photo{left:593px;top:746px;width:64px;height:65px;background:linear-gradient(#e8e8e8,#43506a);border:2px solid var(--white)}
.testi-name{left:666px;top:756px;font-size:10px;font-weight:700;color:#333}
.testi-role{left:666px;top:772px;font-size:8.5px;color:#333}
.testi-site{left:666px;top:787px;font-size:9px;font-style:italic;font-family:"Noto Serif",Georgia,serif;color:#666}
.testi-quote{left:593px;top:819px;width:190px;font-family:"Noto Serif",Georgia,serif;font-style:italic;font-size:9px;line-height:15px;color:#777}

/* footer */
.footer{left:73px;top:941px;width:746px;height:259px;background:var(--footer);border-top:10px solid var(--bar);border-radius:0 0 10px 10px}
.foot-bar{left:73px;top:1152px;width:746px;height:48px;background:var(--footer-deep);border-radius:0 0 10px 10px}
.foot-h{font-size:12px;color:#e6e6e6;display:flex;align-items:center;gap:6px;white-space:nowrap}
.foot-h::after{content:"";display:block;height:1px;background:#5a5a5a;flex:1}
.foot-h.small{font-size:11px}
.foot-list{font-size:8.5px;line-height:15px;color:var(--footer-text)}
.foot-list a{color:var(--footer-text)}
.foot-text{font-size:8.5px;line-height:16.5px;color:var(--footer-text)}
.net{width:24px;height:24px;border-radius:3px;position:absolute}
.news{left:594px;top:1076px;width:198px;height:25px;background:#333;border:1px solid #555;font-size:8px;font-style:italic;color:#888;padding:6px 9px}
.subscribe{left:727px;top:1078px;width:63px;height:21px;background:var(--red);color:var(--white);font-size:9.5px;font-weight:600;line-height:21px;text-align:center;border-radius:2px}
.copy{left:83px;top:1170px;font-size:9px;color:#5c5c5c}
.legal{left:660px;top:1170px;font-size:9px;color:#bbb}
</style>
</head>
<body>

<header>
  <div class="abs brand"><span class="brand-mark"></span><span class="brand-name">Velkor Group</span></div>
  <div class="abs search-label">Velkor Group Search</div>
  <div class="abs search-frame"></div>
  <div class="abs search-box">Search here...</div>
  <svg class="abs search-icon" width="13" height="13" viewBox="0 0 13 13"><circle cx="5" cy="5" r="3.8" fill="none" stroke="#2f8ed4" stroke-width="2"/><line x1="8" y1="8" x2="12" y2="12" stroke="#2f8ed4" stroke-width="2.4"/></svg>
</header>

<nav class="abs nav">
  <span class="nav-item is-active" style="left:8px;width:67px">HOME</span>
  <span class="nav-item" style="left:82px;width:120px">Food &amp; Beverages</span>
  <span class="nav-item" style="left:212px;width:107px">Transportation</span>
  <span class="nav-item" style="left:329px;width:103px">Agro Processing</span>
  <span class="nav-item" style="left:450px;width:102px">Manufacturing</span>
  <span class="social" style="left:633px;background:#3b5998" aria-label="Social link"></span>
  <span class="social" style="left:658px;background:#2ea7de" aria-label="Social link"></span>
  <span class="social" style="left:684px;background:#c8232c" aria-label="Social link"></span>
  <span class="social" style="left:709px;background:#d6282b" aria-label="Social link"></span>
</nav>

<section class="abs hero" role="img" aria-label="Photo of business people taking notes at a conference table"></section>
<div class="abs welcome">
  <h1>Welcome to <span>VELKOR GROUP</span></h1>
  <p>Lorem ipsum dolor sit amet, consectetur adipisicing elit, sed do eiusmod tempor incididunt ut labore et dolore magna aliqua. Ut enim ad minim veniam, quis nostrud exercitation ullamco laboris nisi ut aliquip ex ea commodo consequat.</p>
  <a class="btn-red">Read More <svg width="6" height="7" viewBox="0 0 6 7"><path d="M0 0L6 3.5L0 7Z" fill="#fff"/></svg></a>
</div>
<div class="abs dots"><i class="on"></i><i></i><i></i><i></i></div>

<section class="abs features">
  <div class="feature" style="width:251px">
    <svg style="left:34px;top:26px" width="34" height="50" viewBox="0 0 34 50"><path d="M2 0v16q0 6 5 7v27h5V23q5-1 5-7V0h-3v14h-2V0h-3v14H7V0z" fill="#fff"/><path d="M27 0q7 5 7 20q0 5-3 6v24h-5V0z" fill="#fff"/></svg>
    <h2 style="left:91px">Parents</h2>
    <p style="left:91px">Lorem ipsum dolor sit amet consec-tetur adipisicing elit.</p>
    <a style="left:91px">Read More</a>
  </div>
  <div class="feature" style="width:254px">
    <svg style="left:20px;top:30px" width="52" height="38" viewBox="0 0 52 38"><rect x="0" y="0" width="33" height="26" fill="#fff"/><path d="M35 7h10l7 10v9H35z" fill="#fff"/><circle cx="10" cy="30" r="6" fill="#fff" stroke="#1a80c6" stroke-width="2"/><circle cx="42" cy="30" r="6" fill="#fff" stroke="#1a80c6" stroke-width="2"/></svg>
    <h2 style="left:86px">Transportation</h2>
    <p style="left:88px">Lorem ipsum dolor sit amet consec-tetur adipisicing elit.</p>
    <a style="left:88px">Read More</a>
  </div>
  <div class="feature" style="width:241px">
    <svg style="left:20px;top:26px" width="46" height="46" viewBox="0 0 46 46"><rect x="2" y="2" width="42" height="42" fill="none" stroke="#fff" stroke-width="3"/><path d="M6 24h10l4-10 6 18 4-10h10" fill="none" stroke="#fff" stroke-width="2.5"/></svg>
    <h2 style="left:84px">Businesses</h2>
    <p style="left:84px">Lorem ipsum dolor sit amet consec-tetur adipisicing elit.</p>
    <a style="left:84px">Read More</a>
  </div>
</section>

<section class="abs about"></section>
<div class="abs about-photo" role="img" aria-label="Photo of a smiling businesswoman holding a tablet"></div>
<h2 class="abs about-title">About <span>VELKOR GROUP</span></h2>
<p class="abs about-lead">Lorem ipsum dolor sit amet, consectetur adipisicing elit, sed do eiusmod tempor incididunt ut labore et dolore magna aliqua. Ut enim ad minim veniam, quis nostrud exercitation ullamco laboris nisi ut aliquip ex ea commodo consequat. Duis aute irure dolor in reprehenderit in voluptate velit esse cillum dolore eu fugiat nulla pariatur. Excepteur sint occaecat cupidatat non proident, sunt in culpa qui officia deserunt mollit anim id est laborum.</p>
<p class="abs about-body">Lorem ipsum dolor sit amet, consectetur adipisicing elit, sed do eiusmod tempor incididunt ut labore et dolore magna aliqua quis nostrud exercitation ullamco laboris nisi ut aliquip ex ea commodo consequat. Duis aute irure dolor in reprehenderit in voluptate velit esse cillum dolore eu fugiat nulla pariatur. Excepteur sint occaecat cupidatat non proident, sunt in culpa qui officia deserunt mollit anim id est.</p>
<a class="abs about-more">Read More</a>

<h2 class="abs testi-title">Testimonials</h2>
<div class="abs rule" style="left:702px;top:725px;width:62px"></div>
<div class="abs testi-photo" role="img" aria-label="Portrait photo of the client giving the testimonial"></div>
<div class="abs testi-name">Jonathan Doe</div>
<div class="abs testi-role">Managing Director XYZ</div>
<div class="abs testi-site">Xyz.example</div>
<p class="abs testi-quote">“Donec sed odio dui. Nulla vitae elit libero, a pharetra augue. Nullam id dolor id nibh ultricies vehicula ut id elit. Integer posuere erat a ante venenatis posuere velit aliquet...”</p>

<footer>
  <div class="abs footer"></div>
  <div class="abs foot-bar"></div>

  <div class="abs foot-h" style="left:97px;top:976px;width:115px">Contact Info</div>
  <div class="abs foot-list" style="left:97px;top:1006px;text-decoration:underline">
    <a>lorem ipsum</a><br><a>dolor sit amet 106</a><br><a>1404 consecteture</a><br><a>adipisicing elit</a><br><a>eMail: info@velkorgroup.example</a><br><a>Phone: 1-800-555-0142</a>
  </div>

  <div class="abs foot-h" style="left:250px;top:976px;width:156px">About Us</div>
  <p class="abs foot-text" style="left:250px;top:1006px;width:165px">Lorem ipsum dolor sit amet, consectetur adipisicing elit, sed do eiusmod tempor incididunt ut labore et dolore magna aliqua. Ut enim ad minim veniam.</p>

  <div class="abs foot-h" style="left:442px;top:976px;width:115px">Company Info</div>
  <div class="abs foot-list" style="left:443px;top:1006px;line-height:14px;text-decoration:underline">
    <a>Home</a><br><a>Food &amp; Beverage</a><br><a>Real Estate Development</a><br><a>Transportation</a><br><a>Health Care</a><br><a>Consumer Products Distribution</a><br><a>Agro Processing</a>
  </div>

  <div class="abs foot-h small" style="left:594px;top:977px;width:198px">Stay updates on our Socail Network</div>
  <span class="net" style="left:595px;top:1011px;background:#3b6fb6" aria-label="Social link"></span>
  <span class="net" style="left:629px;top:1011px;background:#4fb3e8" aria-label="Social link"></span>
  <span class="net" style="left:662px;top:1011px;background:#1f7bc0" aria-label="Social link"></span>

  <div class="abs foot-h" style="left:594px;top:1051px;width:198px">Join Our Newsletter</div>
  <div class="abs news">Enter your email address</div>
  <div class="abs subscribe">Subscribe</div>

  <div class="abs copy">Copyright © 2013 velkorgroup.example - All Rights Reserved</div>
  <div class="abs legal">Privacy Policy &nbsp;| &nbsp;Terms &amp; Conditions</div>
</footer>

</body>
</html>
```